Business Card: RW Office Partners - Your organised problem solver

Business Name: RW Office Partners
Website: www.rwofficepartners.com.au
Email: marisol@rwofficepartners.com.au
Mobile: 61 482 907 236
Facebook: @rwofficepartners
Instrgram: @rwofficepartners

Brading Colours:
HEX
#986474
#ddccd3
#7a8498
#c9d8e4
#000000
#ffffff

Tag Line: Your organised problem solver

Link to DRAFT website:
https://deskhelpcollective.wixsite.com/rw-office-partners

About Page from the website:
My name is Marisol Wrenfield, and I would love to assist you to become more productive in your day to day and achieve your business and personal goals.
My mission is to give you time, time to work on the important tasks of your business or to be able to spend more time with your family. I will take on the tasks you don’t have time for, don’t know well or simply don’t like to do.
I have an extensive background in Administration, Tender Coordination, Document Control, WHS and Quality Management working primarily in the Construction, Mining and Corporate World.
I am passionate about being organised, having order and making things in your life (and mine) easier! I love to watch something unfold and grow into something amazing! I am known for being the go-to problem solver, the organiser of all things, producing high standards of work even under pressure. I’m also a confident communicator, and I understand that you’re busy running your business.

Target Market(s)

Small to Medium Business who require assistance in their business by a virtual assistant.

Industry/Entity Type

Virtual Assistant

Contact Information for Business Card

Mobile: 61 482 907 236

Font styles to use
Sans Serif

Colors
ffffff

Requirements
Must have
• Branding Colours as outlined.
Contact Details as outlined.
Logo as provided.
Proper contact details - mobile, facebook, instragm, website.
Simple, Elegant, very clean looking.
Should not have
• Note cute with pictures.
Not too girly as still want to market to construction companies.

```html
<!DOCTYPE html>
<html lang="en">
<head>
<meta charset="utf-8">
<title>RW Office Partners – Business Card</title>
<link href="https://fonts.googleapis.com/css2?family=Montserrat:wght@400;600&display=swap" rel="stylesheet">
<style>
  :root {
    --mauve: #986474;
    --mauve-light: #ddccd3;
    --slate: #7a8498;
    --ink: #1f1b1c;
    --white: #ffffff;
    --backdrop: #e4dfd7;
  }
  * { margin: 0; padding: 0; box-sizing: border-box; }
  html, body {
    width: 1200px; height: 965px; overflow: hidden;
    background: var(--backdrop);
    font-family: "Montserrat", sans-serif;
  }
  .canvas { position: relative; width: 1200px; height: 965px; }
  .card {
    position: absolute; left: 275px; width: 650px; height: 372px;
    border-radius: 26px; overflow: hidden;
    box-shadow: 0 4px 10px rgba(0,0,0,0.18);
  }
  .card--front { top: 90px; background: var(--mauve); }
  .card--back { top: 503px; background: var(--white); }

  .brand-name {
    font-weight: 600; text-transform: uppercase;
    letter-spacing: 0.02em; line-height: 1.08;
  }
  .card--front .brand-name {
    position: absolute; left: 0; right: 0; top: 138px;
    text-align: center; font-size: 48px; color: var(--ink);
  }
  .card--back .brand-name {
    position: absolute; right: 24px; top: 36px;
    text-align: right; font-size: 33px; color: var(--slate);
  }

  .contact-list {
    position: absolute; left: 28px; top: 218px; list-style: none;
  }
  .contact-item {
    display: flex; align-items: center; gap: 8px;
    height: 25.8px; font-size: 17.5px; color: var(--slate);
  }
  .contact-icon { width: 17px; height: 17px; flex: none; }

  .tagline {
    position: absolute; right: 24px; top: 212px;
    text-align: right; text-transform: uppercase;
    font-size: 29px; line-height: 35px; color: var(--slate);
    font-weight: 400; letter-spacing: 0.01em;
  }
</style>
</head>
<body>
<main class="canvas">
  <section class="card card--front" aria-label="Card front">
    <p class="brand-name">RW Office<br>Partners</p>
  </section>

  <section class="card card--back" aria-label="Card back">
    <p class="brand-name">RW Office<br>Partners</p>

    <ul class="contact-list">
      <li class="contact-item">
        <svg class="contact-icon" viewBox="0 0 17 17" aria-hidden="true">
          <rect x="4" y="1" width="9" height="15" rx="1.6" fill="none" stroke="#986474" stroke-width="1.6"/>
          <line x1="7" y1="13.3" x2="10" y2="13.3" stroke="#986474" stroke-width="1.4"/>
        </svg>
        61 482 907 236
      </li>
      <li class="contact-item">
        <svg class="contact-icon" viewBox="0 0 17 17" aria-hidden="true">
          <rect x="1.5" y="1.5" width="14" height="14" rx="2" fill="#986474"/>
        </svg>
        @rwofficepartners
      </li>
      <li class="contact-item">
        <svg class="contact-icon" viewBox="0 0 17 17" aria-hidden="true">
          <rect x="1.5" y="1.5" width="14" height="14" rx="2" fill="#986474"/>
        </svg>
        @rwofficepartners
      </li>
      <li class="contact-item">
        <svg class="contact-icon" viewBox="0 0 17 17" aria-hidden="true">
          <rect x="1" y="3.5" width="15" height="10" fill="#986474"/>
          <polyline points="1,3.5 8.5,9.5 16,3.5" fill="none" stroke="#ffffff" stroke-width="1.3"/>
        </svg>
        marisol@rwofficepartners.com.au
      </li>
      <li class="contact-item">
        <svg class="contact-icon" viewBox="0 0 17 17" aria-hidden="true">
          <circle cx="8.5" cy="8.5" r="7.5" fill="#986474"/>
          <ellipse cx="8.5" cy="8.5" rx="3.2" ry="7.5" fill="none" stroke="#ffffff" stroke-width="1"/>
          <line x1="1" y1="8.5" x2="16" y2="8.5" stroke="#ffffff" stroke-width="1"/>
        </svg>
        www.rwofficepartners.com.au
      </li>
    </ul>

    <p class="tagline">Your<br>Organised<br>Problem<br>Solver</p>
  </section>
</main>
</body>
</html>
```